WE ARE BRIGHT SPARROW, building a full website with ecommerce

requirements:
CODED FOR SITEQUILL
ONLINE STORE FUNCTION WITH E-COMMERCE USING TRADEBLOOM
PAGEWAVE AND PICTOLANE LINKS

I need a website design for my organization, WE ARE BRIGHT SPARROW, a global empowerment movement elevating woman, and the world. The site's home page should reflect our mission, to empower women. It should have a strong, empowering feel, with minimalistic design.
Please see www.lunavelto.com and http://www.corvenhal.co/ for an inspiration on layout and feel.

**PLEASE SEE ATTACHMENT "LOGO MOCK UP" FOR LOGO. THIS IS NOT THE FINAL VECTOR FILE, BUT THIS LOOKS THE SAME AS THE FINAL LOGO.

HOME PAGE:
The first section of the home page should include a background image with our logo center.

You should include the following links to pages at the top right of the page:
MISSION
MANTRA
ARMOR
MEET BS (I would like "bs" to be our logo)
pagewave and pictolane links

As you scroll down the page, you should see the following sections, which correlate to the links to pages as written above. **SEE ATTACHED SKETCH "HOMEPAGE LAYOUT IDEA" FOR REFERENCE**

WHO WE ARE (correlates to the link Mission)

OUR MANTRA (correlates to the link Mantra)

OUR ARMOR (correlates to the link The Shirt)
(This is where we will sell a shirt (and other apparel) and need the e-commerce function)

MEET BRIGHT SPARROWS (correlates to the link Meet BS)

SHOW OFF YOUR SUPER POWERS (correlates to the pagewave and pictolane)

FEATURED BRIGHT SPARROW (no link on top right of page)

On the homepage, for each of the above sections, as you scroll down there should be an image, either in the background or framed, next to the title (WHO WE ARE, for example), as well as one sentence of small text explaining the title. The title (WHO WE ARE) and the one sentence should link to a page (ie WHO WE ARE + the one sentence links to the MISSION page). ** SEE ATTACHED SKETCH "HOMEPAGE SECTION IDEAS" FOR REFERENCE**

**PLEASE SEE ATTACHMENT "WEBSITE TITLE IDEAS" FOR A STARTING PLACE OF THE LOOK. These don't have to be exact, but they give you an idea of what I'm looking for.

**FONTS TYPOLD EXTRA BOLD AND TYPOLD BOOK 500 (WHICH SHOULD BE BOLDED MANUALLY) ARE ATTACHED**

Target Market(s)

Women, mainly in US

Industry/Entity Type

Social

Coding

Coded - Design and coding required

Number of Pages Required

5+ page

Font styles to use
Other font styles liked:
• Typol Extra Bold

Requirements
Must have
• CODED FOR SITEQUILL
• ONLINE STORE FUNCTION WITH E-COMMERCE USING TRADEBLOOM
• PAGEWAVE AND PICTOLANE LINKS
• Typold Extra Bold and Typold Book 500, attached
• please see description for all requirements
Nice to have
• please see description for all ideas
Should not have

```html
<!DOCTYPE html>
<html lang="en">
<head>
<meta charset="utf-8">
<title>We Are Bright Sparrow</title>
<link rel="stylesheet" href="https://fonts.googleapis.com/css2?family=Montserrat:wght@400;500;700;800&family=Hind:wght@400;500&display=swap">
<style>
:root{
  --ink:#2b2b2b;
  --text:#555;
  --white:#fff;
  --band:#f1f1f2;
  --accent:#1ab0c9;
  --footer:#2a2a2a;
  --muted:#9a9a9a;
}
*{box-sizing:border-box;margin:0;padding:0}
html,body{width:1200px;height:3991px;overflow:hidden}
body{background:var(--white);color:var(--ink);font-family:"Hind",sans-serif;position:relative}
.head-font{font-family:"Montserrat",sans-serif}
section,header,footer{position:absolute;left:0;width:1200px}
.mark{display:inline-block;border:4px solid var(--ink);flex:none}

.site-header{top:0;height:141px;display:flex;align-items:center;padding:0 80px}
.brand{display:flex;align-items:center;gap:20px;font-family:"Montserrat",sans-serif;font-weight:800;font-size:30px;line-height:1;letter-spacing:.5px}
.brand .mark{width:44px;height:44px}
.main-nav{margin-left:auto;display:flex;gap:40px;font-family:"Montserrat",sans-serif;font-size:17px;font-weight:500;letter-spacing:.5px}
.main-nav .social{font-size:13px;font-weight:700;color:var(--ink)}

.hero{top:141px;height:537px;background:linear-gradient(90deg,#b7b9bd,#6c6c70 35%,#4a4a4e 55%,#9a9ca0 80%,#c4c5c7);text-align:center;color:var(--white)}
.hero-brand{position:absolute;top:130px;width:100%;font-family:"Montserrat",sans-serif;font-weight:800;font-size:20px;letter-spacing:2px}
.hero h1{position:absolute;top:230px;width:100%;font-family:"Montserrat",sans-serif;font-weight:700;font-size:50px;letter-spacing:1px}
.hero .sub{position:absolute;top:290px;width:100%;font-family:"Montserrat",sans-serif;font-size:32px;letter-spacing:1px}
.signup{position:absolute;left:255px;top:354px;width:690px;height:46px;display:flex}
.signup .field{flex:1;background:var(--white);color:#777;font-size:16px;text-align:left;padding:13px 16px}
.signup .btn{width:147px;background:var(--accent);font-family:"Montserrat",sans-serif;font-weight:700;font-size:17px;padding-top:13px;letter-spacing:1px}

.mission-band{top:678px;height:253px;background:var(--band);text-align:center}
.mission-band p{position:absolute;top:55px;width:100%;font-family:"Montserrat",sans-serif;font-weight:700;font-size:24px;line-height:32px;letter-spacing:1px}
.lets-fly{position:absolute;top:150px;left:0;width:100%;display:flex;justify-content:center;align-items:center;gap:14px;font-family:"Montserrat",sans-serif;font-size:22px;line-height:22px;text-align:left}
.lets-fly .mark{width:34px;height:34px;border-width:3px}
.lets-fly b{font-weight:800}

.feature{height:0}
.photo{position:absolute}
.feature-title{position:absolute;display:flex;gap:24px;align-items:flex-start;font-family:"Montserrat",sans-serif;font-size:38px;line-height:38px;letter-spacing:1px}
.feature-title .mark{width:60px;height:60px;margin-top:6px}
.feature-title b{font-weight:800}
.feature-text{position:absolute;width:520px;font-size:16px;line-height:26px;color:var(--text)}

.who{top:931px;height:492px;background:var(--white)}
.mantra{top:1423px;height:479px;background:var(--band)}
.meet{top:1902px;height:484px;background:var(--white)}
.armor{top:2386px;height:620px;background:var(--band)}
.powers{top:3006px;height:284px;background:var(--white)}
.featured{top:3290px;height:527px;background:var(--band)}

.armor .feature-title{left:0;width:100%;justify-content:center;top:60px}
.product{position:absolute;top:160px;width:330px;height:394px;background:var(--white);text-align:center}
.product .shot{position:absolute;left:100px;top:20px;width:130px;height:170px}
.product h3{position:absolute;top:205px;width:100%;font-family:"Montserrat",sans-serif;font-size:15px;font-weight:700}
.product p{position:absolute;top:232px;left:40px;width:250px;font-size:15px;line-height:20px;color:var(--text)}
.product .price{position:absolute;top:285px;width:100%;font-family:"Montserrat",sans-serif;font-weight:700;font-size:24px;color:var(--accent)}
.product .shop{position:absolute;left:82px;top:327px;width:166px;height:46px;background:var(--accent);color:var(--white);font-family:"Montserrat",sans-serif;font-weight:700;font-size:15px;padding-top:15px}

.powers-inner{position:absolute;top:70px;left:0;width:100%;display:flex;justify-content:center;align-items:center;gap:26px}
.powers-inner .mark{width:100px;height:100px;border-width:6px}
.powers-title{font-family:"Montserrat",sans-serif;font-size:20px;line-height:22px;letter-spacing:1px}
.powers-title b{display:block;font-weight:800;font-size:40px;line-height:42px}
.powers-links{margin-left:28px;display:flex;gap:30px;font-family:"Montserrat",sans-serif;font-weight:700;font-size:20px;color:#666}

.site-footer{top:3817px;height:174px;background:var(--footer);color:#ccc;text-align:center}
.footer-brand{position:absolute;top:28px;width:100%;font-family:"Montserrat",sans-serif;font-weight:800;font-size:18px;color:var(--white);letter-spacing:1px}
.footer-nav{position:absolute;top:68px;width:100%;display:flex;justify-content:center;gap:60px;font-family:"Montserrat",sans-serif;font-size:15px;letter-spacing:.5px}
.copyright{position:absolute;top:98px;width:100%;font-size:12px}
.footer-social{position:absolute;top:128px;width:100%;display:flex;justify-content:center;gap:24px;font-family:"Montserrat",sans-serif;font-size:12px;font-weight:700;color:var(--muted)}
</style>
</head>
<body>

<header class="site-header">
  <div class="brand"><span class="mark"></span><span>WE ARE<br>BRIGHT<br>SPARROW</span></div>
  <nav class="main-nav">
    <span>MISSION</span><span>MANTRA</span><span>MEET BS</span><span>THE SHIRT</span>
    <span class="social">PAGEWAVE</span><span class="social">PICTOLANE</span>
  </nav>
</header>

<section class="hero" role="img" aria-label="Photo of a confident woman in front of blurred colleagues">
  <div class="hero-brand">BRIGHT SPARROW</div>
  <h1>I AM A BRIGHT SPARROW</h1>
  <div class="sub">AND I WILL CONQUER THE WORLD</div>
  <div class="signup"><span class="field">brightsparrows@email.com</span><span class="btn">LET'S FLY</span></div>
</section>

<section class="mission-band">
  <p>WE ARE BRIGHT SPARROW IS A GLOBAL EMPOWERMENT MOVEMENT<br>ELEVATING WOMEN... AND THE WORLD.</p>
  <div class="lets-fly"><span class="mark"></span><span>LET'S<br><b>FLY</b></span></div>
</section>

<section class="feature who">
  <div class="photo" style="left:0;top:72px;width:524px;height:372px;background:linear-gradient(135deg,#dfe6ec,#a9b4bd 50%,#6f665f)" role="img" aria-label="Photo of women in a business meeting"></div>
  <div class="feature-title" style="left:590px;top:120px"><span class="mark"></span><span>WHO<br>WE<br><b>ARE</b></span></div>
  <p class="feature-text" style="left:590px;top:256px">Aliquam molestie, mi et imperdiet euismod, dui purus auctor tellus, et interdum lacus lectus et ante. Sed accumsan sollicitudin sapien, sit amet adipiscing turpis gravida ac. In congue, neque ac lobortis volutpat, libero mauris varius mi.</p>
</section>

<section class="feature mantra">
  <div class="feature-title" style="left:80px;top:104px"><span class="mark"></span><span><b>OUR</b><br>MANTRA</span></div>
  <p class="feature-text" style="left:80px;top:190px">Aliquam molestie, mi et imperdiet euismod, dui purus auctor tellus, et interdum lacus lectus et ante. Sed accumsan sollicitudin sapien, sit amet adipiscing turpis gravida ac. In congue, neque ac lobortis volutpat, libero mauris varius mi.</p>
  <div class="photo" style="left:676px;top:53px;width:524px;height:375px;background:linear-gradient(180deg,#b9c9d6,#8a9aa6 60%,#5d5650)" role="img" aria-label="Photo of a businesswoman meditating on a wooden deck"></div>
</section>

<section class="feature meet">
  <div class="photo" style="left:0;top:48px;width:524px;height:372px;background:linear-gradient(135deg,#e6e6e4,#b4aa9c 50%,#7a7470)" role="img" aria-label="Photo of three businesswomen standing together"></div>
  <div class="feature-title" style="left:590px;top:110px"><span class="mark"></span><span>MEET<br><b>BRIGHT</b><br>SPARROWS</span></div>
  <p class="feature-text" style="left:590px;top:246px">Aliquam molestie, mi et imperdiet euismod, dui purus auctor tellus, et interdum lacus lectus et ante. Sed accumsan sollicitudin sapien, sit amet adipiscing turpis gravida ac. In congue, neque ac lobortis volutpat, libero mauris varius mi.</p>
</section>

<section class="armor">
  <div class="feature-title"><span class="mark"></span><span><b>OUR</b><br>ARMOR</span></div>
  <div class="product" style="left:75px">
    <div class="shot" style="background:linear-gradient(180deg,#d8c2ad,#a9c4dd)" role="img" aria-label="Photo of a woman in a light blue shirt"></div>
    <h3>PRODUCT NAME</h3><p>Vestibulum ante ipsum primis in faucibus orci luctus.</p>
    <div class="price">$10.00</div><div class="shop">SHOP NOW</div>
  </div>
  <div class="product" style="left:436px">
    <div class="shot" style="background:linear-gradient(180deg,#2b45a8,#1c2f80)" role="img" aria-label="Photo of a blue blazer"></div>
    <h3>PRODUCT NAME</h3><p>Vestibulum ante ipsum primis in faucibus orci luctus.</p>
    <div class="price">$10.00</div><div class="shop">SHOP NOW</div>
  </div>
  <div class="product" style="left:795px">
    <div class="shot" style="background:linear-gradient(180deg,#2a2d3a,#1a1c25)" role="img" aria-label="Photo of a navy blazer"></div>
    <h3>PRODUCT NAME</h3><p>Vestibulum ante ipsum primis in faucibus orci luctus.</p>
    <div class="price">$10.00</div><div class="shop">SHOP NOW</div>
  </div>
</section>

<section class="powers">
  <div class="powers-inner">
    <span class="mark"></span>
    <div class="powers-title">SHOW OFF YOUR<b>SUPER<br>POWERS</b></div>
    <div class="powers-links"><span>PAGEWAVE</span><span>PICTOLANE</span></div>
  </div>
</section>

<section class="feature featured">
  <div class="feature-title" style="left:80px;top:86px"><span class="mark"></span><span>FEATURED<br><b>BRIGHT</b><br><b>SPARROWS</b></span></div>
  <p class="feature-text" style="left:80px;top:230px">Aliquam molestie, mi et imperdiet euismod, dui purus auctor tellus, et interdum lacus lectus et ante. Sed accumsan sollicitudin sapien, sit amet adipiscing turpis gravida ac. In congue, neque ac lobortis volutpat, libero mauris varius mi.</p>
  <div class="photo" style="left:676px;top:54px;width:524px;height:375px;background:linear-gradient(135deg,#e8eef3,#b7c2cb 55%,#3a3a40)" role="img" aria-label="Photo of a smiling businesswoman holding papers"></div>
</section>

<footer class="site-footer">
  <div class="footer-brand">BRIGHT SPARROW</div>
  <nav class="footer-nav"><span>MISSION</span><span>MANTRA</span><span>MEET BS</span><span>THE SHIRT</span></nav>
  <p class="copyright">Copyright © 2017. Company Name All Right Reserved</p>
  <div class="footer-social"><span>PAGEWAVE</span><span>PICTOLANE</span></div>
</footer>

</body>
</html>
```